Young, dynamic furniture company needs a new business card design

We require a new business card design for our modern furniture company which supplies furniture and appliances to the property and development market.
Oakridge Interiors has become one of the leading furniture & appliance suppliers to the property market withing London. With over 10 years experience, we have increased our business to supply not only private landlords and managing agents, but also property developers, housing associations and local councils.
We offer not only a complete range of furniture which includes beds, wardrobes, dining sets and sofas, but also a high quality, full delivery and assembly service to help you with all our furnishing needs.

Target Market(s)

Private landlords, estate agents, letting agents, property management companies

Industry/Entity Type

Business

Contact Information for Business Card

Name,
Title,
Address,
Mobile,
Telephone,
Fax, Website, email address

Font styles to use
Sans Serif

Colors
3176b5
0555a3
85abd2
cfdeed

Requirements
Must have
• All the above information for each of our staff, along with our logo

```html
<!DOCTYPE html>
<html lang="en">
<head>
<meta charset="utf-8">
<title>Oakridge Interiors – Business Card</title>
<link href="https://fonts.googleapis.com/css2?family=Montserrat:wght@500;700&family=Roboto+Condensed:wght@400&family=Varela+Round&display=swap" rel="stylesheet">
<style>
  :root {
    --page-bg: #d8d4cf;
    --card-top: #f1f2f3;
    --card-bottom: #e4e7ea;
    --ink: #1e1f22;
    --brand-blue: #0555a3;
    --name-blue: #1d4f8a;
    --icon-navy: #244a73;
    --band: #3a5f80;
    --band-text: #e6edf4;
    --rule: #4d7394;
  }
  * { margin: 0; padding: 0; box-sizing: border-box; }
  html, body { width: 970px; height: 1200px; overflow: hidden; }
  body { background: var(--page-bg); position: relative; }

  .card {
    position: absolute;
    left: 170px; top: 40px;
    width: 630px; height: 1120px;
    background: linear-gradient(170deg, var(--card-top), var(--card-bottom));
    box-shadow: 0 10px 30px rgba(0,0,0,0.18);
    overflow: hidden;
  }

  .brand-mark {
    position: absolute;
    left: 50%; top: 110px;
    width: 150px; height: 150px;
    transform: translateX(-50%);
    background: var(--brand-blue);
  }
  .brand-name {
    position: absolute;
    left: 0; right: 0; top: 385px;
    text-align: center;
    font-family: "Roboto Condensed", sans-serif;
    font-weight: 400;
    font-size: 48px;
    color: var(--ink);
    letter-spacing: 0.5px;
  }
  .brand-tagline {
    position: absolute;
    left: 0; right: 0; top: 447px;
    text-align: center;
    font-family: "Roboto Condensed", sans-serif;
    font-size: 25px;
    color: var(--ink);
  }

  .person { position: absolute; left: 83px; top: 575px; }
  .person-name {
    font-family: "Montserrat", sans-serif;
    font-weight: 700;
    font-size: 40px;
    color: var(--name-blue);
    line-height: 1;
  }
  .person-title {
    font-family: "Montserrat", sans-serif;
    font-weight: 500;
    font-size: 28px;
    color: var(--ink);
    margin-top: 2px;
  }

  .address {
    position: absolute; left: 83px; top: 705px;
    font-family: "Varela Round", sans-serif;
    font-size: 30px;
    line-height: 44px;
    color: var(--ink);
  }

  .contacts {
    position: absolute; left: 83px; top: 800px;
    list-style: none;
    font-family: "Varela Round", sans-serif;
    font-size: 32px;
    color: var(--ink);
  }
  .contacts li { display: flex; align-items: center; height: 43px; }
  .contact-icon { width: 37px; height: 37px; margin-right: 14px; flex: none; }

  .footer-rule {
    position: absolute; left: 0; right: 0; top: 1024px;
    height: 4px; background: var(--rule);
  }
  .footer-band {
    position: absolute; left: 0; right: 0; top: 1034px; bottom: 0;
    background: var(--band);
    display: flex; align-items: center; justify-content: center;
    font-family: "Varela Round", sans-serif;
    font-size: 30px;
    color: var(--band-text);
    letter-spacing: 0.5px;
  }
</style>
</head>
<body>
  <main class="card">
    <div class="brand-mark"></div>
    <div class="brand-name">OAKRIDGE INTERIORS</div>
    <div class="brand-tagline">TRADE FURNITURE SOLUTIONS</div>

    <div class="person">
      <div class="person-name">DANIEL HARPER</div>
      <div class="person-title">Maneger</div>
    </div>

    <address class="address" style="font-style:normal">
      Your Address,2nd Ste<br>
      Millbrook, Texas 1234, USA
    </address>

    <ul class="contacts">
      <li>
        <svg class="contact-icon" viewBox="0 0 37 37" aria-hidden="true">
          <rect width="37" height="37" fill="var(--icon-navy)"/>
          <path d="M13 8 l4 5 -2.5 2.5 c1.5 3 3.5 5 6.5 6.5 l2.5 -2.5 5 4 -2.5 4 c-8 0 -16 -8 -16 -16z" fill="#fff"/>
        </svg>
        123 456 7890
      </li>
      <li>
        <svg class="contact-icon" viewBox="0 0 37 37" aria-hidden="true">
          <rect width="37" height="37" fill="var(--icon-navy)"/>
          <rect x="12" y="8" width="13" height="7" fill="#fff"/>
          <rect x="7" y="15" width="23" height="10" rx="1.5" fill="#fff"/>
          <rect x="12" y="22" width="13" height="8" fill="#fff" stroke="var(--icon-navy)" stroke-width="1.5"/>
        </svg>
        123 456 7890
      </li>
      <li>
        <svg class="contact-icon" viewBox="0 0 37 37" aria-hidden="true">
          <rect width="37" height="37" fill="var(--icon-navy)"/>
          <rect x="12" y="6" width="13" height="25" rx="2" fill="#fff"/>
          <rect x="14.5" y="9" width="8" height="8" fill="var(--icon-navy)"/>
          <circle cx="18.5" cy="26" r="1.6" fill="var(--icon-navy)"/>
        </svg>
        123 456 7890
      </li>
      <li>
        <svg class="contact-icon" viewBox="0 0 37 37" aria-hidden="true">
          <rect width="37" height="37" fill="var(--icon-navy)"/>
          <rect x="7" y="11" width="23" height="15" fill="#fff"/>
          <path d="M7 11 l11.5 9 11.5 -9" fill="none" stroke="var(--icon-navy)" stroke-width="1.6"/>
        </svg>
        your@yourcompany.com
      </li>
    </ul>

    <div class="footer-rule"></div>
    <div class="footer-band">www.yourcompany.com</div>
  </main>
</body>
</html>
```